Commercial/Corporate Law Firm needs Website Design

Hi guys. I've started up a new law firm and would love your help designing an attractive website. I'll need both design and coding, and to make it easy for us to edit as necessary later, I think it should be built off a Wordpress.org structure.
FIRST IMPRESSIONS
It's very important that the first impression of the website really captures our prospective clients' attention and impresses them. Their first three seconds needs to be good.
I imagine the homepage may be short, with a menu bar and a compelling image, and with a tagline overlaid or underneath (eg. "It's about results.")
The image should be related to our practice areas: eg. IPOs, corporate transactions, or commercial negotiations.
I have previously suggested there could be a skyline image of Sydney or Adelaide. However, because we are based in Adelaide, I don't think Sydney is appropriate - and Adelaide is probably too boring to use.
HOMEPAGE
Being a new firm, we don't have many existing testimonials, and I will be the only lawyer to start with. So we need to focus on the nature of the services we will provide and how my experience can help them. We have an existing logo to use, and I would like the website colour scheme not to clash with that logo (dark blue and white).
After the initial image and tagline there should be a brief introduction to each of the main areas of work, eg. "We specialise in three main areas of practice:"
1. Corporate Transactions and Regulation
2. Business Law and Dispute Resolution
3. Migration Assistance
These should each have an appropriate photo and link to a separate page that briefly describes our services in that area.
Below that there should be a message from me with a photo. Finally, at the bottom, there should be a "Contact Us" section which shows a Google image of our address, contact details, and then our logo with colours inverted.
OTHER PAGES
While we will need some other pages, they should all be fairly simple. I think we will need one page to say "About Us", where I will put information about my experience. I think we will then need one page for each of the 3 areas listed above, which just needs an appropriate image and then text to describe the service. Finally, a "Contact Us" page which I imagine will be the same as the bottom of the homepage.
OTHER DETAILS
For now you can use details from my LinkedIn page to fill out any other text as necessary, or the photo.
Because the logo is square, I would prefer the design of the website also to be rectangular.
Looking forward to seeing your work! Thank you.
Marcus
Potential clients:
Businesses with legal issues or disputes
Companies wishing to list on the stock market

```html
<!DOCTYPE html>
<html lang="en">
<head>
<meta charset="utf-8">
<title>Calder Legal</title>
<link href="https://fonts.googleapis.com/css2?family=Cinzel:wght@400;600&family=Catamaran:wght@800&family=Arimo:wght@400&display=swap" rel="stylesheet">
<style>
:root{
  --navy:#1b3768;
  --navy-deep:#142a52;
  --ink:#1e3561;
  --grey-btn:#6b6b6b;
  --grey-text:#6e6e6e;
  --white:#ffffff;
  --nav-active:#707070;
  --contact-dark:#1c232c;
}
*{margin:0;padding:0;box-sizing:border-box}
html,body{width:691px;height:1200px;overflow:hidden;background:var(--white)}
body{position:relative;font-family:"Arimo",Arial,sans-serif;color:var(--grey-text)}
.abs{position:absolute}
.serif{font-family:"Cinzel",Georgia,serif}

/* header */
.site-header{left:0;top:0;width:691px;height:54px;background:var(--white)}
.brand{left:44px;top:0;width:130px;height:77px;z-index:3}
.brand-tab{position:absolute;left:0;top:0}
.brand-mark{position:absolute;left:51px;top:10px;width:28px;height:28px;background:var(--navy)}
.brand-name{position:absolute;left:0;width:130px;top:44px;text-align:center;font-family:"Cinzel",Georgia,serif;font-weight:600;font-size:13.5px;color:var(--navy);letter-spacing:1px;line-height:1.15}
.call{left:512px;top:14px}
.call-label{position:absolute;left:31px;top:0;font-size:9px;color:#444;white-space:nowrap}
.call-number{position:absolute;left:31px;top:10px;font-size:17px;color:var(--navy);white-space:nowrap}

.main-nav{left:0;top:54px;width:691px;height:36px;background:var(--navy)}
.nav-item{position:absolute;top:0;height:36px;line-height:36px;font-size:9.5px;color:var(--white);text-align:center}
.nav-item.active{background:var(--nav-active)}

/* hero */
.hero{left:0;top:90px;width:691px;height:300px;background:linear-gradient(90deg,#cfd3d8 0%,#bfb9ae 40%,#8f9aa8 62%,#2b3448 80%,#c9cfd6 100%)}
.hero-title{left:44px;top:172px;font-family:"Catamaran",Arial,sans-serif;font-weight:800;font-size:29px;color:var(--navy);letter-spacing:-0.3px;z-index:2}
.hero-text{left:46px;top:212px;width:290px;font-size:10px;line-height:17px;color:var(--navy);z-index:2}
.btn{display:block;background:var(--grey-btn);color:var(--white);font-family:"Cinzel",Georgia,serif;font-size:13px;letter-spacing:.5px;text-align:center}
.hero-btn{left:45px;top:270px;width:114px;height:29px;line-height:29px;z-index:2}
.slide-arrow{width:29px;height:29px;border-radius:50%;background:rgba(40,60,90,.55);top:221px;z-index:2}

/* services */
.services{left:0;top:390px;width:691px;height:204px;background:var(--navy)}
.service{position:absolute;top:0;width:200px;text-align:center}
.service-badge{position:absolute;top:-40px;left:60px;width:80px;height:80px;border-radius:50%;background:var(--white);border:2px solid var(--navy)}
.service-badge svg{position:absolute;left:18px;top:18px}
.service-title{position:absolute;top:52px;left:0;width:200px;font-family:"Cinzel",Georgia,serif;font-size:11px;line-height:16px;color:var(--white);letter-spacing:.4px}
.service-text{position:absolute;top:92px;left:0;width:200px;font-size:8.3px;line-height:15px;color:#d6dcea}
.service-arrow{position:absolute;top:164px;left:90px}

/* about */
.about-photo{left:76px;top:616px;width:176px;height:205px;border-radius:80px 80px 0 0;background:linear-gradient(180deg,#e9ddd2 0%,#3b3b4a 45%,#2b2c3a 100%)}
.about-title{left:298px;top:632px;font-family:"Cinzel",Georgia,serif;font-weight:600;font-size:27px;color:var(--navy);letter-spacing:1px}
.about-text{left:298px;top:668px;width:320px;font-size:8.3px;line-height:15px;color:var(--grey-text)}
.about-text p+p{margin-top:4px}
.about-btn{left:298px;top:753px;width:114px;height:30px;line-height:30px}

/* contact */
.contact{left:0;top:821px;width:691px;height:258px;background:linear-gradient(180deg,#2a323d 0%,#1c232c 55%,#141a22 100%)}
.contact-title{left:46px;top:910px;font-family:"Cinzel",Georgia,serif;font-size:26px;color:var(--white);letter-spacing:1px}
.contact-sub{left:46px;top:947px;font-size:9px;color:var(--white)}
.field{position:absolute;background:var(--white);font-size:8px;color:#666;padding:9px 9px}
.contact-btn{left:327px;top:988px;width:114px;height:30px;line-height:30px}

/* footer */
.footer-mark{left:327px;top:1058px;width:36px;height:36px;background:var(--navy);border:3px solid var(--white);outline:1px solid #cfd6e2}
.footer-heading{font-family:"Cinzel",Georgia,serif;font-size:10px;color:var(--navy);letter-spacing:.6px}
.quick-links{left:46px;top:1125px;list-style:none;font-size:8px;color:var(--navy)}
.quick-links li{height:17px;position:relative;padding-left:13px}
.quick-links li::before{content:"";position:absolute;left:0;top:3px;width:4px;height:4px;background:var(--navy)}
.footer-line{font-size:8px;color:var(--navy);white-space:nowrap}
.social-box{left:504px;top:1124px;width:24px;height:24px;background:var(--navy);border:2px solid #cfd6e2}
.copyright{left:504px;top:1157px;width:150px;font-size:8px;line-height:12px;color:#777}
.copyright span{color:var(--navy)}
</style>
</head>
<body>

<header class="site-header abs"></header>

<div class="brand abs">
  <svg class="brand-tab" width="130" height="77" viewBox="0 0 130 77"><path d="M0 0H130V54L122 77H8L0 54Z" fill="#ffffff"/></svg>
  <span class="brand-mark"></span>
  <div class="brand-name">CALDER<br><span style="font-size:8px;letter-spacing:5px">LEGAL</span></div>
</div>

<div class="call abs">
  <svg width="26" height="26" viewBox="0 0 24 24"><path fill="#1b3768" d="M6.6 10.8c1.4 2.8 3.8 5.1 6.6 6.6l2.2-2.2c.3-.3.7-.4 1-.2 1.1.4 2.3.6 3.6.6.6 0 1 .4 1 1V20c0 .6-.4 1-1 1C10.6 21 3 13.4 3 4c0-.6.4-1 1-1h3.5c.6 0 1 .4 1 1 0 1.3.2 2.5.6 3.6.1.3 0 .7-.2 1z"/></svg>
  <span class="call-label">Call Us Today :</span>
  <span class="call-number">555 014 2298</span>
</div>

<nav class="main-nav abs">
  <span class="nav-item active" style="left:311px;width:66px">HOME</span>
  <span class="nav-item" style="left:392px;width:46px">ABOUT</span>
  <span class="nav-item" style="left:447px;width:88px">PRACTICE AREAS</span>
  <span class="nav-item" style="left:545px;width:70px">CONTACT US</span>
  <svg class="abs" style="left:635px;top:12px" width="12" height="12" viewBox="0 0 12 12"><circle cx="5" cy="5" r="3.6" fill="none" stroke="#fff" stroke-width="1.8"/><path d="M7.6 7.6L11 11" stroke="#fff" stroke-width="2"/></svg>
</nav>

<section class="hero abs" role="img" aria-label="Smiling lawyer in a suit with arms crossed, colleagues in a bright office behind"></section>
<h1 class="hero-title abs">IT'S ABOUT RESULTS</h1>
<p class="hero-text abs">Lorem Ipsum is simply dummy text of the printing and type setting industry Lorem Ipsum has Lorem Ipsum is simply dummy text of the printing and type.</p>
<a class="btn hero-btn abs">CONTACT US</a>
<span class="slide-arrow abs" style="left:7px"><svg width="29" height="29" viewBox="0 0 29 29"><path d="M16.5 9l-5 5.5 5 5.5" fill="none" stroke="#fff" stroke-width="1"/></svg></span>
<span class="slide-arrow abs" style="left:654px"><svg width="29" height="29" viewBox="0 0 29 29"><path d="M12.5 9l5 5.5-5 5.5" fill="none" stroke="#fff" stroke-width="1"/></svg></span>

<section class="services abs">
  <div class="service" style="left:43px">
    <span class="service-badge"><svg width="44" height="44" viewBox="0 0 44 44" fill="none" stroke="#1b3768" stroke-width="2"><rect x="4" y="8" width="36" height="24"/><path d="M16 38h12M22 32v6"/><circle cx="26" cy="20" r="6"/><path d="M12 4v14M8 14l4 4 4-4"/></svg></span>
    <h3 class="service-title">CORPORATE TRANSACTIONS<br>AND REGULATION</h3>
    <p class="service-text">Lorem Ipsum is simply dummy text of the printing and typesetting industry Lorem Ipsum is simply dummy text of the printing and typesetting industry.</p>
    <svg class="service-arrow" width="20" height="10" viewBox="0 0 20 10"><path d="M0 5h17M13 1l5 4-5 4" fill="none" stroke="#fff" stroke-width="2"/></svg>
  </div>
  <div class="service" style="left:246px">
    <span class="service-badge"><svg width="44" height="44" viewBox="0 0 44 44" fill="none" stroke="#1b3768" stroke-width="2"><path d="M6 36l16-16"/><rect x="18" y="6" width="12" height="18" transform="rotate(45 24 15)"/><path d="M24 40h14v-4H24z"/></svg></span>
    <h3 class="service-title">BUSINESS LAW AND DISPUTE<br>RESOLUTION</h3>
    <p class="service-text">Lorem Ipsum is simply dummy text of the printing and typesetting industry Lorem Ipsum is simply dummy text of the printing and typesetting industry.</p>
    <svg class="service-arrow" width="20" height="10" viewBox="0 0 20 10"><path d="M0 5h17M13 1l5 4-5 4" fill="none" stroke="#fff" stroke-width="2"/></svg>
  </div>
  <div class="service" style="left:450px">
    <span class="service-badge"><svg width="44" height="44" viewBox="0 0 44 44" fill="none" stroke="#1b3768" stroke-width="2"><path d="M10 22a12 12 0 0 1 24 0"/><rect x="7" y="20" width="5" height="9" rx="2"/><rect x="32" y="20" width="5" height="9" rx="2"/><path d="M34 29q0 6-8 6h-4"/><path d="M8 42q0-6 14-6t14 6"/></svg></span>
    <h3 class="service-title">MIGRATION<br>ASSISTANCE</h3>
    <p class="service-text">Lorem Ipsum is simply dummy text of the printing and typesetting industry Lorem Ipsum is simply dummy text of the printing and typesetting industry.</p>
    <svg class="service-arrow" width="20" height="10" viewBox="0 0 20 10"><path d="M0 5h17M13 1l5 4-5 4" fill="none" stroke="#fff" stroke-width="2"/></svg>
  </div>
</section>

<div class="about-photo abs" role="img" aria-label="Portrait of the principal lawyer in a dark suit and red tie"></div>
<h2 class="about-title abs">ABOUT US</h2>
<div class="about-text abs">
  <p>Lorem Ipsum is simply dummy text of the printing and typesetting industry. Lorem Ipsum has been the industry's standard dummy text ever.</p>
  <p>Lorem Ipsum is simply dummy text of the printing and typesetting industry. Lorem Ipsum has been the industry's standard dummy text ever since the 1500s, when an unknown printer took a galley of type and scrambled.</p>
</div>
<a class="btn about-btn abs">CONTACT US</a>

<section class="contact abs" role="img" aria-label="Silhouettes of a business meeting around a table against bright windows"></section>
<h2 class="contact-title abs">CONTACT US</h2>
<p class="contact-sub abs">Need An Have Question Please Contact Us Today.</p>
<span class="field" style="left:327px;top:860px;width:156px;height:27px">Name *</span>
<span class="field" style="left:490px;top:860px;width:156px;height:27px">Email *</span>
<span class="field" style="left:327px;top:894px;width:319px;height:26px">Phone *</span>
<span class="field" style="left:327px;top:927px;width:319px;height:54px">Message *</span>
<a class="btn contact-btn abs">CONTACT US</a>

<span class="footer-mark abs"></span>

<h4 class="footer-heading abs" style="left:46px;top:1103px">QUICK LINK</h4>
<ul class="quick-links abs">
  <li>Home</li><li>About</li><li>Practice Areas</li><li>Contact</li>
</ul>

<h4 class="footer-heading abs" style="left:198px;top:1103px">CONTACT US</h4>
<svg class="abs" style="left:198px;top:1124px" width="12" height="12" viewBox="0 0 24 24"><path fill="#1b3768" d="M6.6 10.8c1.4 2.8 3.8 5.1 6.6 6.6l2.2-2.2c.3-.3.7-.4 1-.2 1.1.4 2.3.6 3.6.6.6 0 1 .4 1 1V20c0 .6-.4 1-1 1C10.6 21 3 13.4 3 4c0-.6.4-1 1-1h3.5c.6 0 1 .4 1 1 0 1.3.2 2.5.6 3.6.1.3 0 .7-.2 1z"/></svg>
<span class="footer-line abs" style="left:219px;top:1127px">555 014 2298</span>
<svg class="abs" style="left:198px;top:1146px" width="12" height="10" viewBox="0 0 12 10"><rect width="12" height="10" rx="1" fill="#1b3768"/><path d="M1 1.5l5 4 5-4" fill="none" stroke="#fff" stroke-width="1.2"/></svg>
<span class="footer-line abs" style="left:219px;top:1147px">info@calderlegal.com</span>

<svg class="abs" style="left:351px;top:1124px" width="12" height="17" viewBox="0 0 12 17"><path d="M6 0a6 6 0 0 1 6 6c0 4.5-6 11-6 11S0 10.5 0 6a6 6 0 0 1 6-6z" fill="#1b3768"/><circle cx="6" cy="6" r="2.2" fill="#fff"/></svg>
<span class="footer-line abs" style="left:371px;top:1124px;line-height:13px">101 - Lorem is the simple text<br>print and type text.</span>

<span class="social-box abs"></span>
<p class="copyright abs">©<span>CALDER LEGAL</span> - 2018 All Right Reserved.</p>

</body>
</html>
```